Verlindo Magician

I want the business card for my business to give to people who watch that later I will be employed to show magic here is my website http://www.verlindoillusions.example/I want the interesting design , i am very opened for formal and informal, I watch a lot of design so don't stick to the common shape and form but i hope it can also be produced the thing to write on will be the same as in picture that i will upload , i also will upload the logo for you that so can be easy to useDenis CostilleMagicianMAGICIAN BALSAMO 17 rue des Tilleuls - 25000 BESANÇON contact@verlindoillusions.example tel. 0381 946 157 tel. 0674 219 503

```html
<!DOCTYPE html>
<html lang="fr">
<head>
<meta charset="utf-8">
<title>Verlindo Magician – business card</title>
<link rel="stylesheet" href="https://fonts.googleapis.com/css2?family=Roboto:wght@300;400;500;700&display=swap">
<style>
  :root {
    --backdrop: #939498;
    --shadow: #58585a;
    --card: #ffffff;
    --ink: #111111;
    --portrait: #1a1a1a;
  }
  * { margin: 0; padding: 0; box-sizing: border-box; }
  html, body { width: 1200px; height: 1200px; overflow: hidden; }
  body {
    position: relative;
    background: var(--backdrop);
    font-family: "Roboto", Arial, sans-serif;
    color: var(--ink);
  }
  .card-shadow { position: absolute; width: 804px; height: 473px; background: var(--shadow); }
  .card { position: absolute; left: 190px; width: 820px; height: 482px; background: var(--card); }
  .card--front { top: 77px; }
  .card--back { top: 619px; }
  .portrait { position: absolute; background: linear-gradient(180deg, #2a2a2a, var(--portrait)); border-radius: 46% 46% 18% 18% / 30% 30% 14% 14%; }
  .brand-name { position: absolute; font-weight: 300; letter-spacing: 0.04em; text-align: center; white-space: nowrap; }

  .card--front .portrait { left: 122px; top: 135px; width: 140px; height: 176px; }
  .card--front .brand-name { left: 92px; width: 200px; top: 314px; font-size: 28px; }

  .details { position: absolute; left: 412px; top: 100px; }
  .details__name { font-size: 41px; font-weight: 700; line-height: 1; letter-spacing: 0.005em; }
  .details__role { font-size: 22px; font-weight: 500; line-height: 1; margin-top: 6px; }
  .contact-group { margin-top: 20px; }
  .contact-group + .contact-group { margin-top: 28px; }
  .contact { display: flex; align-items: flex-start; font-size: 23px; line-height: 27px; }
  .contact svg { width: 18px; height: 18px; margin-top: 4px; margin-right: 8px; flex: none; }

  .card--back .portrait { left: 322px; top: 85px; width: 192px; height: 240px; }
  .card--back .brand-name { left: 218px; width: 400px; top: 330px; font-size: 40px; }
  .card--back .web { position: absolute; left: 0; width: 100%; top: 446px; text-align: center; font-size: 22px; }
</style>
</head>
<body>
  <div class="card-shadow" style="left:234px; top:109px;"></div>
  <section class="card card--front">
    <div class="portrait" role="img" aria-label="Black and white illustration of the magician in a dark jacket holding a playing card"></div>
    <div class="brand-name">VERLINDO</div>

    <div class="details">
      <h1 class="details__name">MARC RAVOULET</h1>
      <p class="details__role">MAGICIAN</p>

      <div class="contact-group">
        <p class="contact"><svg viewBox="0 0 20 20"><circle cx="10" cy="10" r="9" fill="none" stroke="#111" stroke-width="1.4"/><path d="M6 5l2 0 1 3-1.3 1a7 7 0 0 0 3.3 3.3L12 11l3 1v2a1 1 0 0 1-1 1A9 9 0 0 1 5 6a1 1 0 0 1 1-1z" fill="#111"/></svg>0381 946 157</p>
        <p class="contact"><svg viewBox="0 0 20 20"><circle cx="10" cy="10" r="9" fill="#111"/><rect x="5.5" y="8" width="9" height="6" rx="1" fill="#fff"/><rect x="5" y="5.5" width="10" height="2" rx="1" fill="#fff"/></svg>0674 219 503</p>
      </div>

      <div class="contact-group">
        <p class="contact"><svg viewBox="0 0 20 20"><circle cx="10" cy="10" r="9" fill="#111"/><rect x="5" y="6.5" width="10" height="7" fill="#fff"/><path d="M5 6.5l5 4 5-4" fill="none" stroke="#111" stroke-width="1"/></svg>contact@verlindoillusions.example</p>
        <p class="contact"><svg viewBox="0 0 20 20"><circle cx="10" cy="10" r="8.5" fill="none" stroke="#111" stroke-width="1.6"/><ellipse cx="10" cy="10" rx="3.5" ry="8.5" fill="none" stroke="#111" stroke-width="1.3"/><path d="M1.5 10h17M3 6h14M3 14h14" stroke="#111" stroke-width="1.2"/></svg>www.verlindoillusions.example</p>
      </div>

      <div class="contact-group">
        <p class="contact"><svg viewBox="0 0 20 20"><path d="M10 2L1 10h3v8h4.5v-5h3v5H16v-8h3z" fill="#111"/></svg><span>17 rue des Tilleuls -<br>25000 BESANÇON</span></p>
      </div>
    </div>
  </section>

  <div class="card-shadow" style="left:234px; top:654px;"></div>
  <section class="card card--back">
    <div class="portrait" role="img" aria-label="Large black and white illustration of the magician in a dark jacket holding a playing card"></div>
    <div class="brand-name">VERLINDO</div>
    <p class="web">www.verlindoillusions.example</p>
  </section>
</body>
</html>
```